Business card design for international hub site

I need a business card design with the logo attached. Although the site is for the teenage audience (it is about the high school graduation ball, the Prom), the business card is for professional use to be given to professional contacts (B2B), such as suppliers and partners, so it needs to look professional (but also girly, glamours and clean).

Target Market(s)

B2B

Industry/Entity Type

Media

Colors
eea4c8
f9d9e8
e667a6
9d9d9d
1b1b1b

Requirements
Must have
• Space for Name, Tile, Address, Phone, email and website.
Should not have
• Photo

```html
<!DOCTYPE html>
<html lang="en">
<head>
<meta charset="utf-8">
<title>The Dance Bloom – Business Card</title>
<link rel="stylesheet" href="https://fonts.googleapis.com/css2?family=Arimo:wght@400;700&display=swap">
<style>
  :root {
    --pink-soft: #f9d9e8;
    --pink-mid: #eea4c8;
    --pink-hot: #e667a6;
    --magenta: #c2246f;
    --plum: #6e1f55;
    --plum-deep: #5a1846;
    --grey: #9d9d9d;
    --ink: #1b1b1b;
    --white: #ffffff;
    --stage: #2b2b2b;
  }
  * { margin: 0; padding: 0; box-sizing: border-box; }
  html, body {
    width: 1200px; height: 997px; overflow: hidden;
    background: var(--stage);
    font-family: "Arimo", Arial, sans-serif;
  }
  .sheet { position: relative; width: 1200px; height: 997px; }
  .card {
    position: absolute; left: 220px; width: 760px; height: 434px;
    border-radius: 22px; overflow: hidden;
    box-shadow: 0 18px 40px rgba(0,0,0,.45);
  }

  /* Front */
  .card-front {
    top: 36px;
    background: linear-gradient(180deg, #e27fc6 0%, #efaedc 45%, #f3c4e4 70%, #e6a6d2 100%);
  }
  .front-moon {
    position: absolute; right: 48px; top: 44px;
    width: 250px; height: 250px; border-radius: 50%;
    background: radial-gradient(circle, #fdf2f8 0%, #f8e1ee 70%, #f1cde4 100%);
    display: flex; align-items: center; justify-content: center;
  }
  .brand-name {
    font-size: 30px; font-weight: 400; color: var(--plum); letter-spacing: .3px;
    text-align: center; line-height: 1.15;
  }
  .front-horizon { position: absolute; left: 0; bottom: 0; width: 760px; height: 200px; }
  .front-illustration {
    position: absolute; left: 30px; top: 150px; width: 330px; height: 284px;
    border-radius: 160px 160px 0 0;
    background: linear-gradient(180deg, rgba(150,40,110,.35) 0%, rgba(120,30,90,.6) 60%, rgba(90,24,70,.85) 100%);
  }

  /* Back */
  .card-back {
    top: 516px;
    background: linear-gradient(100deg, #e8529a 0%, #ef7fb2 28%, #f6c0d8 52%, #fbe9f1 72%, #f5f2f4 100%);
  }
  .back-ornament {
    position: absolute; right: 40px; top: 36px; width: 280px; height: 360px;
    border-radius: 140px 140px 24px 24px;
    background: linear-gradient(160deg, rgba(214,60,140,.28) 0%, rgba(194,36,111,.42) 55%, rgba(150,30,95,.5) 100%);
  }
  .back-content { position: absolute; left: 40px; top: 40px; color: var(--white); }
  .back-brand { font-size: 36px; font-weight: 400; line-height: 1.05; margin-bottom: 42px; }
  .person-name { font-size: 19px; font-weight: 700; color: var(--magenta); letter-spacing: 1px; }
  .person-title { font-size: 15px; color: var(--white); margin-top: 3px; margin-bottom: 22px; }
  .contact-list { list-style: none; }
  .contact-item {
    display: flex; align-items: flex-start; gap: 10px;
    font-size: 17px; line-height: 1.2; margin-bottom: 6px; color: var(--white);
  }
  .contact-icon {
    flex: 0 0 20px; width: 20px; height: 20px; border-radius: 50%;
    background: var(--white); display: flex; align-items: center; justify-content: center;
    margin-top: 1px;
  }
  .contact-icon svg { width: 12px; height: 12px; fill: var(--pink-hot); }
  .website { margin-top: 16px; font-size: 19px; font-weight: 700; color: var(--magenta); }
</style>
</head>
<body>
<main class="sheet">
  <section class="card card-front">
    <div class="front-moon">
      <span class="brand-name">The Dance<br>Bloom</span>
    </div>
    <svg class="front-horizon" viewBox="0 0 760 200" preserveAspectRatio="none" aria-hidden="true">
      <path d="M0 120 C180 90 300 110 420 60 C520 30 640 40 760 20 L760 200 L0 200 Z" fill="#b45a9c" opacity=".55"/>
      <path d="M0 165 C200 140 420 150 760 110 L760 200 L0 200 Z" fill="#5a1846" opacity=".85"/>
    </svg>
    <div class="front-illustration" role="img" aria-label="Illustration: silhouettes of grass, hearts and swirling flowers with two birds flying in a pink dusk sky"></div>
  </section>

  <section class="card card-back">
    <div class="back-ornament" role="img" aria-label="Ornament: magenta floral swirl with blossoms, leaves and vines"></div>
    <div class="back-content">
      <div class="back-brand">The Dance Bloom</div>
      <div class="person-name">LENA MARLOWE</div>
      <div class="person-title">Marketing Director</div>
      <ul class="contact-list">
        <li class="contact-item">
          <span class="contact-icon"><svg viewBox="0 0 12 12"><path d="M2.5 1h2l1 2.5-1.3 1a6 6 0 0 0 3.3 3.3l1-1.3L11 7.5v2a1 1 0 0 1-1 1A9 9 0 0 1 1.5 2a1 1 0 0 1 1-1z"/></svg></span>
          <span>(800) 555-0142</span>
        </li>
        <li class="contact-item">
          <span class="contact-icon"><svg viewBox="0 0 12 12"><path d="M2.5 1h2l1 2.5-1.3 1a6 6 0 0 0 3.3 3.3l1-1.3L11 7.5v2a1 1 0 0 1-1 1A9 9 0 0 1 1.5 2a1 1 0 0 1 1-1z"/></svg></span>
          <span>(706) 555-0187</span>
        </li>
        <li class="contact-item">
          <span class="contact-icon"><svg viewBox="0 0 12 12"><path d="M1 3h10v6.5H1z M1 3l5 3.5L11 3" stroke="#e667a6" stroke-width="1" fill="none"/></svg></span>
          <span>lmarlowe@velvetlane.com</span>
        </li>
        <li class="contact-item">
          <span class="contact-icon"><svg viewBox="0 0 12 12"><path d="M6 1a3.5 3.5 0 0 0-3.5 3.5C2.5 7.5 6 11 6 11s3.5-3.5 3.5-6.5A3.5 3.5 0 0 0 6 1zm0 5a1.4 1.4 0 1 1 0-2.8A1.4 1.4 0 0 1 6 6z"/></svg></span>
          <span>48 Orchard Row, 2nd Floor<br>Riverton, GA 30000</span>
        </li>
      </ul>
      <div class="website">www.velvetlane.com</div>
    </div>
  </section>
</main>
</body>
</html>
```